Business Card Design

We need a business card designed for our new company. Prefer a black card with white logo & writing.

Contact Information for Business Card

Ted Galloway, address: 7-4812 Fernhollow Road, Abbotsford, BC, V3K 8R2, Office Phone: 604-712-3390, Cell: 604-947-2164, Email: ted@resinworkshub.ca

Colors

Designer to choose only greyscale colors for use in the design.

```html
<!DOCTYPE html>
<html lang="en">
<head>
<meta charset="utf-8">
<title>Resin Works Hub — Business Card</title>
<link rel="stylesheet" href="https://fonts.googleapis.com/css2?family=Poppins:wght@400;500;700&display=swap">
<style>
  :root {
    --page-bg: #6f6f71;
    --card-dark: #1c1c1c;
    --card-light: #ffffff;
    --ink: #1a1a1a;
    --ink-soft: #2c2c2c;
    --mark-on-dark: #8a8a8a;
  }
  * { margin: 0; padding: 0; box-sizing: border-box; }
  html, body { width: 900px; height: 1200px; overflow: hidden; }
  body {
    background: var(--page-bg);
    font-family: "Poppins", sans-serif;
    position: relative;
  }
  .card {
    position: absolute;
    left: 134px;
    width: 632px;
    height: 362px;
  }
  .card--front { top: 212px; background: var(--card-dark); }
  .card--back { top: 628px; background: var(--card-light); color: var(--ink); }

  .wordmark {
    font-weight: 700;
    text-align: center;
    line-height: 1;
    white-space: nowrap;
  }
  .wordmark__line { display: block; }
  .wordmark__sub { display: block; letter-spacing: 0.5em; margin-top: 12px; }

  .card--front .wordmark {
    position: absolute;
    left: 0; right: 0; top: 50%;
    transform: translateY(-50%);
    color: var(--mark-on-dark);
    font-size: 50px;
  }
  .card--front .wordmark__sub { font-size: 22px; padding-left: 0.5em; }

  .card--back .wordmark {
    position: absolute;
    left: 20px; width: 310px;
    top: 142px;
    color: var(--ink);
    font-size: 36px;
  }
  .card--back .wordmark__sub { font-size: 18px; padding-left: 0.5em; margin-top: 8px; }

  .divider {
    position: absolute;
    left: 340px; top: 88px;
    width: 3px; height: 182px;
    background: var(--ink);
  }

  .contact {
    position: absolute;
    left: 374px; top: 86px;
  }
  .contact__name {
    font-size: 23px;
    font-weight: 700;
    letter-spacing: 0.02em;
    line-height: 1.2;
  }
  .contact__role {
    font-size: 14px;
    color: var(--ink-soft);
    margin-top: 2px;
  }
  .contact__address {
    font-size: 14px;
    color: var(--ink-soft);
    line-height: 1.5;
    margin-top: 6px;
  }
  .contact__list { list-style: none; margin-top: 10px; }
  .contact__item {
    display: flex;
    align-items: center;
    gap: 8px;
    font-size: 14px;
    line-height: 22.5px;
    color: var(--ink-soft);
  }
  .contact__item--phone { letter-spacing: 0.14em; }
  .contact__icon { width: 13px; height: 13px; flex: none; }
</style>
</head>
<body>

  <section class="card card--front" aria-label="Card front">
    <div class="wordmark">
      <span class="wordmark__line">RESIN WORKS</span>
      <span class="wordmark__sub">HUB</span>
    </div>
  </section>

  <section class="card card--back" aria-label="Card back">
    <div class="wordmark">
      <span class="wordmark__line">RESIN WORKS</span>
      <span class="wordmark__sub">HUB</span>
    </div>

    <div class="divider"></div>

    <div class="contact">
      <h1 class="contact__name">TED GALLOWAY</h1>
      <p class="contact__role">Manager</p>
      <p class="contact__address">7-4812 Fernhollow Road,<br>Abbotsford, BC, V3K 8R2</p>
      <ul class="contact__list">
        <li class="contact__item contact__item--phone">
          <svg class="contact__icon" viewBox="0 0 16 16" aria-hidden="true"><path fill="#1a1a1a" d="M3.6 1.2l2.3 2.6-1.3 1.6c.9 2 2.3 3.5 4.3 4.4l1.6-1.3 2.6 2.3-1.2 2.2C6.5 12.8 3 9.4 1.4 3.3z"/></svg>
          604-712-3390
        </li>
        <li class="contact__item contact__item--phone">
          <svg class="contact__icon" viewBox="0 0 16 16" aria-hidden="true"><rect x="4" y="1" width="8" height="14" rx="1.5" fill="none" stroke="#1a1a1a" stroke-width="1.6"/><circle cx="8" cy="12.4" r="0.9" fill="#1a1a1a"/></svg>
          604-947-2164
        </li>
        <li class="contact__item">
          <svg class="contact__icon" viewBox="0 0 16 16" aria-hidden="true"><rect x="1" y="3.5" width="14" height="9" fill="#1a1a1a"/><path d="M1.5 4l6.5 5 6.5-5" fill="none" stroke="#fff" stroke-width="1.2"/></svg>
          ted@resinworkshub.ca
        </li>
        <li class="contact__item">
          <svg class="contact__icon" viewBox="0 0 16 16" aria-hidden="true"><circle cx="8" cy="8" r="6.3" fill="none" stroke="#1a1a1a" stroke-width="1.5"/><ellipse cx="8" cy="8" rx="2.7" ry="6.3" fill="none" stroke="#1a1a1a" stroke-width="1.2"/><path d="M2 8h12" stroke="#1a1a1a" stroke-width="1.2"/></svg>
          www.resinworkshub.ca
        </li>
      </ul>
    </div>
  </section>

</body>
</html>
```